"Harbor Builders" is a residential building company and needs a new business card design and may re

We would like a redesign based on the existing logo, and would like to see a new font as well. We are bespoke home builders who build sustainable energy efficient homes.

Industry/Entity Type

Construction

Contact Information for Business Card

Business card size 40mm x 90mm

Colors

Designer to choose colors to be used in the design.

```html
<!DOCTYPE html>
<html lang="en">
<head>
<meta charset="utf-8">
<title>Harbor Builders — Business Card</title>
<link rel="stylesheet" href="https://fonts.googleapis.com/css2?family=Open+Sans:wght@400;600&family=Quicksand:wght@400;700&display=swap">
<style>
  :root {
    --backdrop: #2b2b2b;
    --card-light: #ffffff;
    --card-light-fade: #eeeeee;
    --card-dark: #232323;
    --ink: #4a4a4a;
    --ink-soft: #5c5c5c;
    --accent: #8cc63f;
    --mark-grey: #5a5a5a;
    --mark-light: #d9d9d9;
  }
  * { margin: 0; padding: 0; box-sizing: border-box; }
  html, body { width: 1058px; height: 1200px; overflow: hidden; background: var(--backdrop); }
  .canvas { position: relative; width: 1058px; height: 1200px; }

  .card {
    position: absolute; left: 99px; width: 860px; height: 382px;
    box-shadow: 0 14px 30px rgba(0,0,0,0.45);
  }
  .card--front { top: 178px; background: linear-gradient(180deg, var(--card-light) 55%, var(--card-light-fade) 100%); }
  .card--back { top: 640px; background: var(--card-dark); }

  .wordmark {
    position: absolute; display: flex; align-items: center; gap: 16px;
    font-family: "Quicksand", sans-serif; font-weight: 400; white-space: nowrap;
  }
  .wordmark__square { display: block; }
  .card--front .wordmark { top: 52px; right: 48px; font-size: 46px; color: var(--mark-grey); }
  .card--front .wordmark__square { width: 46px; height: 46px; background: var(--accent); }
  .card--back .wordmark { top: 150px; left: 50%; transform: translateX(-50%); font-size: 64px; color: var(--mark-light); }
  .card--back .wordmark__square { width: 64px; height: 64px; background: var(--accent); }

  .contact-person { position: absolute; top: 118px; left: 48px; font-family: "Quicksand", sans-serif; color: var(--ink); }
  .contact-person__name { font-size: 33px; font-weight: 400; letter-spacing: 0.3px; }
  .contact-person__name strong { font-weight: 700; }
  .contact-person__phone { font-family: "Open Sans", sans-serif; font-size: 27px; margin-top: 2px; color: var(--ink-soft); }

  .contact-list { position: absolute; left: 62px; top: 222px; list-style: none; font-family: "Open Sans", sans-serif; font-size: 19px; color: var(--ink); }
  .contact-list li { display: flex; align-items: center; gap: 12px; height: 32px; }
  .contact-list svg { width: 20px; height: 20px; flex: none; }
  .registration { position: absolute; left: 62px; top: 322px; font-family: "Open Sans", sans-serif; font-size: 19px; color: var(--accent); }
</style>
</head>
<body>
<main class="canvas">
  <section class="card card--front" aria-label="Business card front">
    <div class="wordmark"><span class="wordmark__square"></span><span>harbor builders</span></div>

    <div class="contact-person">
      <p class="contact-person__name">Daniel <strong>Marsh</strong></p>
      <p class="contact-person__phone">0400 123 789</p>
    </div>

    <ul class="contact-list">
      <li>
        <svg viewBox="0 0 20 20" aria-hidden="true"><rect x="1" y="4" width="18" height="12" fill="#8cc63f"/><path d="M1 4 L10 11 L19 4" fill="none" stroke="#fff" stroke-width="1.5"/></svg>
        daniel@harborbuilders.com.au
      </li>
      <li>
        <svg viewBox="0 0 20 20" aria-hidden="true"><g fill="none" stroke="#8cc63f" stroke-width="1.4"><circle cx="10" cy="10" r="8.5"/><ellipse cx="10" cy="10" rx="3.8" ry="8.5"/><line x1="1.5" y1="10" x2="18.5" y2="10"/><line x1="3" y1="5.5" x2="17" y2="5.5"/><line x1="3" y1="14.5" x2="17" y2="14.5"/></g></svg>
        www.harborbuilders.com.au
      </li>
      <li>
        <svg viewBox="0 0 20 20" aria-hidden="true"><path d="M10 1 C5.6 1 3 4.2 3 7.6 C3 12.5 10 19 10 19 C10 19 17 12.5 17 7.6 C17 4.2 14.4 1 10 1 Z" fill="#8cc63f"/><circle cx="10" cy="7.6" r="2.6" fill="#fff"/></svg>
        PO Box 4127 Northgate LPO Bayview WA 6120
      </li>
    </ul>
    <p class="registration">Registration 40581 ABN: 52 309 614 778</p>
  </section>

  <section class="card card--back" aria-label="Business card back">
    <div class="wordmark"><span class="wordmark__square"></span><span>harbor builders</span></div>
  </section>
</main>
</body>
</html>
```